Executive Business Card for Healthcare Company [Need Today]

I need a business card design for a healthcare company. The only branding the company has thus far is a logo. The cards will be utilized by company executives. The design I envision will be vibrant and appealing but with a corporate feel. They shouldn't be too casual or playful. I would like to complete this project TODAY if possible.

Target Market(s)

Healthcare vendors, other executives in healthcare and pharmaceuticals

Industry/Entity Type

Pharmaceutical

Contact Information for Business Card

See attachment

Font styles to use
Serif
Sans Serif

Colors

Designer to choose colors to be used in the design.

```html
<!DOCTYPE html>
<html lang="en">
<head>
<meta charset="utf-8">
<title>Corvan Therapeutics – Business Card</title>
<link rel="stylesheet" href="https://fonts.googleapis.com/css2?family=Open+Sans:wght@400;600&family=Rubik:wght@400;500&display=swap">
<style>
  :root {
    --backdrop: #e4e4e4;
    --card: #ffffff;
    --teal: #36bfc7;
    --teal-text: #2fb6c0;
    --ink: #555a5e;
    --shadow: rgba(0,0,0,0.28);
  }
  * { box-sizing: border-box; margin: 0; padding: 0; }
  html, body { width: 1200px; height: 1000px; overflow: hidden; }
  body {
    background: var(--backdrop);
    position: relative;
    font-family: "Open Sans", sans-serif;
  }
  .card {
    position: absolute;
    width: 636px;
    height: 362px;
    background: var(--card);
    border-radius: 32px;
    overflow: hidden;
    box-shadow: 0 6px 14px var(--shadow);
  }
  .card-front { left: 145px; top: 98px; }
  .card-back { left: 368px; top: 545px; }

  .front-brand {
    position: absolute;
    left: 100px;
    top: 118px;
    display: flex;
    align-items: center;
    gap: 28px;
  }
  .brand-mark {
    width: 136px;
    height: 136px;
    border: 4px solid var(--teal);
    border-radius: 50%;
    flex: none;
  }
  .brand-name {
    color: var(--teal-text);
    font-family: "Open Sans", sans-serif;
    font-weight: 400;
    line-height: 1;
  }
  .front-brand .brand-name .primary { display: block; font-size: 62px; letter-spacing: 1px; }
  .front-brand .brand-name .secondary { display: block; font-size: 27px; margin-top: 4px; text-align: right; }

  .back-band {
    position: absolute;
    left: 0; top: 0;
    width: 100%;
    height: 180px;
    background: var(--teal);
  }
  .holder {
    position: absolute;
    left: 42px;
    top: 72px;
    color: #fff;
  }
  .holder-name {
    font-family: "Rubik", sans-serif;
    font-weight: 400;
    font-size: 32px;
    letter-spacing: 2px;
    line-height: 1;
  }
  .holder-title {
    font-family: "Rubik", sans-serif;
    font-weight: 500;
    font-size: 18px;
    margin-top: 12px;
  }
  .back-brand {
    position: absolute;
    left: 366px;
    top: 64px;
    display: flex;
    align-items: center;
    gap: 12px;
  }
  .back-brand .brand-mark {
    width: 72px; height: 72px;
    border: 2.5px solid #fff;
  }
  .back-brand .brand-name { color: #fff; }
  .back-brand .brand-name .primary { display: block; font-size: 32px; }
  .back-brand .brand-name .secondary { display: block; font-size: 14px; text-align: right; margin-top: 2px; }

  .contact-list {
    position: absolute;
    left: 40px;
    top: 198px;
    list-style: none;
    color: var(--ink);
    font-size: 22px;
    letter-spacing: 0.6px;
  }
  .contact-list li {
    display: flex;
    align-items: center;
    height: 29px;
  }
  .contact-list svg { width: 20px; height: 20px; margin-right: 18px; fill: var(--ink); }

  .company-line {
    position: absolute;
    left: 0; right: 0;
    top: 306px;
    text-align: center;
    color: var(--teal-text);
    font-size: 16px;
    line-height: 20px;
  }
</style>
</head>
<body>

<section class="card card-front" aria-label="Card front">
  <div class="front-brand">
    <div class="brand-mark"></div>
    <div class="brand-name">
      <span class="primary">corvan</span>
      <span class="secondary">therapeutics</span>
    </div>
  </div>
</section>

<section class="card card-back" aria-label="Card back">
  <div class="back-band"></div>
  <div class="holder">
    <div class="holder-name">Daniel Hale</div>
    <div class="holder-title">Senior Director of Marketing</div>
  </div>
  <div class="back-brand">
    <div class="brand-mark"></div>
    <div class="brand-name">
      <span class="primary">corvan</span>
      <span class="secondary">therapeutics</span>
    </div>
  </div>

  <ul class="contact-list">
    <li>
      <svg viewBox="0 0 20 20" aria-hidden="true"><path d="M2 6c0-2 3-3 8-3s8 1 8 3v1.5h-4V6H6v1.5H2z"/><rect x="3" y="9" width="14" height="8" rx="1.5"/><circle cx="10" cy="13" r="2" fill="#fff"/></svg>
      555-214-0187
    </li>
    <li>
      <svg viewBox="0 0 20 20" aria-hidden="true"><path d="M4 2.5l3 -0.5 2 4-2 1.5c1 2.5 2.5 4 5 5l1.5-2 4 2-0.5 3c-7 1-14-6-13-13z"/></svg>
      555-214-0263
    </li>
    <li>
      <svg viewBox="0 0 20 20" aria-hidden="true"><path d="M2 5h16v10H2z"/><path d="M2 5l8 6 8-6" fill="none" stroke="#fff" stroke-width="1.5"/></svg>
      dhale@corvanrx.com
    </li>
  </ul>

  <div class="company-line">
    CORVAN THERAPEUTICS, LLC<br>
    180 Linden Avenue, Fairview, GA 30310
  </div>
</section>

</body>
</html>
```